Bram Keystone Homes needs a business card

We need a business card for a new company in Canada, Ontario. Our company is all about luxury contraction homes for our clients. Our product and services are custom projects design. Under the business logo that will be created, we want a slogan that will be a memorable phrase for consumers to remember us to tell their friends and relatives.

Additional infomation
- Ludovic Entrasse
- President / Ceo
-519.604.3087

Find point what luxury construction products and services can be done

We like to see colors:
- #663300
- and something other colors or color that would attract the client needs and wants

The final design should communicate leads from new or old clients that will grow our empire. Most of all, we try to work among the budget that clients want

NOTE
- we also need an icon for the business (Example: Instagram, Facebook, and Whatsapp icons)
- We want the company name to be remembered easily for clients and our distributors who would get our orders.
- we need an icon on the business cards: Facebook and Instagram.

Thanks,
Bram Keystone Homes

```html
<!DOCTYPE html>
<html lang="en">
<head>
<meta charset="utf-8">
<title>Bram Keystone Homes — Business Card</title>
<link rel="stylesheet" href="https://fonts.googleapis.com/css2?family=Work+Sans:wght@400;500;700&display=swap">
<style>
  :root {
    --backdrop: #1a1a1a;
    --card: #232323;
    --card-edge: #2b2b2b;
    --ink-light: #e9e9e9;
    --ink-soft: #bdbdbd;
    --brand-brown: #663300;
    --accent-copper: #8a4b1d;
  }
  * { margin: 0; padding: 0; box-sizing: border-box; }
  html, body {
    width: 1200px; height: 900px; overflow: hidden;
    background: var(--backdrop);
    font-family: "Work Sans", sans-serif;
  }
  .stage {
    position: relative; width: 1200px; height: 900px;
  }
  .card {
    position: absolute; left: 290px; width: 620px; height: 354px;
    background: linear-gradient(135deg, var(--card) 0%, var(--card-edge) 100%);
    box-shadow: 0 14px 30px rgba(0,0,0,0.55);
  }
  .card--front { top: 70px; }
  .card--back { top: 476px; }

  .front-brand {
    position: absolute; left: 0; right: 0; top: 138px; text-align: center;
  }
  .brand-name {
    font-size: 36px; font-weight: 700; color: var(--ink-light);
    letter-spacing: 0.5px;
  }
  .brand-slogan {
    margin-top: 8px; font-size: 12.5px; font-weight: 500;
    color: var(--ink-soft); letter-spacing: 1.6px;
  }

  .person {
    position: absolute; right: 370px; top: 140px; text-align: right;
  }
  .person-name {
    font-size: 22px; font-weight: 500; color: var(--accent-copper);
  }
  .person-title {
    margin-top: 4px; font-size: 17px; color: var(--ink-light);
  }
  .divider {
    position: absolute; left: 268px; top: 150px; width: 1px; height: 64px;
    background: var(--brand-brown);
  }
  .contacts {
    position: absolute; left: 288px; top: 154px; list-style: none;
  }
  .contacts li {
    display: flex; align-items: center; gap: 10px;
    font-size: 16.5px; color: var(--ink-light); line-height: 22px;
  }
  .contacts svg { width: 11px; height: 11px; flex: none; }
  .address {
    position: absolute; left: 0; right: 0; top: 290px; text-align: center;
    font-size: 17px; color: var(--ink-light); letter-spacing: 0.4px;
  }
</style>
</head>
<body>
<main class="stage">
  <section class="card card--front" aria-label="Card front">
    <div class="front-brand">
      <div class="brand-name">Bram Keystone Homes</div>
      <div class="brand-slogan">- HOME RENOVATIONS - CUSTOM PROJECT DESIGN -</div>
    </div>
  </section>

  <section class="card card--back" aria-label="Card back">
    <div class="person">
      <div class="person-name">Ludovic Entrasse</div>
      <div class="person-title">President / Ceo</div>
    </div>
    <div class="divider"></div>
    <ul class="contacts">
      <li>
        <svg viewBox="0 0 12 12" aria-hidden="true"><path d="M3 1 L5 3.5 L4 4.8 C4.6 6 6 7.4 7.2 8 L8.5 7 L11 9 L9.8 11 C5.5 10.5 1.5 6.5 1 2.2 Z" fill="none" stroke="#8a4b1d" stroke-width="1"/></svg>
        519.604.3087
      </li>
      <li>
        <svg viewBox="0 0 12 12" aria-hidden="true"><rect x="1" y="2.5" width="10" height="7" fill="none" stroke="#8a4b1d" stroke-width="1"/><path d="M1 2.5 L6 6.5 L11 2.5" fill="none" stroke="#8a4b1d" stroke-width="1"/></svg>
        info@bramkeystone.com
      </li>
      <li>
        <svg viewBox="0 0 12 12" aria-hidden="true"><circle cx="6" cy="6" r="5" fill="none" stroke="#8a4b1d" stroke-width="1"/><ellipse cx="6" cy="6" rx="2.2" ry="5" fill="none" stroke="#8a4b1d" stroke-width="0.8"/><path d="M1 6 H11" stroke="#8a4b1d" stroke-width="0.8"/></svg>
        www.bramkeystone.com
      </li>
    </ul>
    <div class="address">2187 Alder Crescent Guelph, ON N1H 4K9</div>
  </section>
</main>
</body>
</html>
```